Community coffee table book/quiz book

I need a couple of things for my book:
- Book cover (Title: "1000 spørsmål om Kvernhaugen")
- "Cover pages" for each chapter of the book (15-16 chapters)
- "Watermark" or background design for all the pages of the book.
- A cover image for the book's Kretsbok page.
- Design of a paper "belt"

The book:
The book will consist of about 200+ pages with ten questions on one page and ten answers on the next.

The name of the book is "1000 spørsmål om Kvernhaugen" which means 1000 questions about Kvernhaugen (Kvernhaugen is a suburb of the city Bergen in Norway). Author is Helge Myrvold.
The questions in the book are grouped in chapters like:
History
Facts
Schools
Businesses
People/profiles
Sport
Culture
Buildings/Landmarks/Sculptures
The different areas of the suburb
The city
Language/expressions
Nature
The names of the chapters are not set, so it would be good to have the option to change the title of the pages without having to contact the designer (maybe by adding the text on top of the cover page?). I therefore suggest that these images are without text.
The book size is 18X18 cm.

The chapter cover pages:
The book will basically consist of text. Ten questions on one page, and ten questions on the next. Visually it will be quite "boring" to look at. I would therefore like to have a chapter cover page for each chapter, preferable in colour.

Water mark:
To avoid having a book full of white pages with limited amount of text I thought of having some kind of design on each page. I do not know how this should be done, but maybe it is possible to create some kind of background image or watermark image with similar design as the book cover and the chapter covers?

The Kretsbok cover image:
This should be the same as, or similar to, the book cover.
I believe the optimal size is 828px x 315px?

Paper "belt":
The book is to be sold for charity. The receiver of the money is the local sports club. I would like to have the book "wrapped in a 5-6 cm wide paper belt with the logo of the sports club (please see logo and colours here: http://www.ilbrattlia.no). I do not think that the book cover itself should have the sports club's color (purple), but maybe the paper band could? (Again: YOU are the designer)

Photos:
I reckon you would like some photos for both the book cover and the chapter covers. I will of course do the best I can to provide these photos when I have selected a designer. I the meantime

Target Market(s)

Target market is middle clas men and women 35+ from the geographical area Kvernhaugen.

Industry/Entity Type

Community

Font styles to use
Serif
Sans Serif

Requirements
Must have
• The book will be sold by children on doors. The buyers will probably take a look briefly through the book and then decide if they are going to buy.
• It is important that they like the question types, categories and some of the actual questions they read. But it is also important that they like the look of the book. Therefore the book cover and the chapter cover pages must be appealing enough for the buyers to want this book on theor coffee table.
Nice to have
• I have uploaded a short video clip to Vidtrekk (https://www.vidtrekk.example/watch?v=qx7Ta2Lm9pz). This a promo clip from Pimlo Kanalen. I felt inspired when I saw it and thought that backgrounds like the ones used in the promo could also be used as backgrounds for each chapter's cover pages. Maybe different colour for each chapter? Screenshots from the clip is uploaded below.
• Then again: Maybe I am an idiot? YOU are the designer :-)
Should not have
• There has been some rivalry between two sportsclubs in the region after the clubs was merged a couple of years ago. I therefore believe we should therefore try avoid both the old clubs' colours (blue&yellow and green) and the new club's colour (purple).

```html
<!DOCTYPE html>
<html lang="no">
<head>
<meta charset="utf-8">
<title>1000 spørsmål om Kvernhaugen – Book cover</title>
<link rel="stylesheet" href="https://fonts.googleapis.com/css2?family=Archivo+Black&family=Oswald:wght@400&family=Josefin+Sans:wght@400&family=Dancing+Script:wght@700&family=Comic+Neue:wght@700&family=PT+Sans+Narrow:wght@400&display=swap">
<style>
  :root {
    --magenta: #ec008c;
    --magenta-deep: #d6007f;
    --sunflower: #ffc905;
    --title-yellow: #ffd400;
    --blush: #f8c6d1;
    --peach: #fcd9c0;
    --white: #ffffff;
    --ink: #1a1a1a;
  }
  html, body {
    margin: 0;
    padding: 0;
    overflow: hidden;
    background: var(--white);
  }
  .canvas {
    position: relative;
    width: 1200px;
    height: 1000px;
    background: var(--white);
    overflow: hidden;
  }
  .cover {
    position: absolute;
    left: 215px;
    top: 40px;
    width: 802px;
    height: 802px;
    background: var(--magenta);
    overflow: hidden;
  }
  .cover-shapes {
    position: absolute;
    inset: 0;
  }
  .cover-text {
    position: absolute;
    inset: 0;
  }
  .count-box {
    position: absolute;
    left: 258px;
    top: 153px;
    width: 314px;
    height: 139px;
    background: var(--blush);
    display: flex;
    align-items: center;
    justify-content: center;
    font-family: "Oswald", sans-serif;
    font-weight: 400;
    font-size: 118px;
    line-height: 1;
    letter-spacing: 30px;
    padding-left: 30px;
    box-sizing: border-box;
    color: var(--magenta);
  }
  .count-rule {
    position: absolute;
    left: 263px;
    top: 302px;
    width: 302px;
    border-top: 3px dotted var(--sunflower);
  }
  .main-title {
    position: absolute;
    left: 0;
    width: 830px;
    top: 290px;
    margin: 0;
    text-align: center;
    font-family: "Archivo Black", sans-serif;
    font-weight: 400;
    font-size: 128px;
    line-height: 1.1;
    letter-spacing: -4px;
    color: var(--peach);
  }
  .connector {
    position: absolute;
    left: 127px;
    top: 432px;
    width: 580px;
    display: flex;
    align-items: center;
    gap: 14px;
  }
  .connector-line {
    flex: 1;
    height: 3px;
    background: var(--white);
  }
  .connector-word {
    font-family: "Dancing Script", cursive;
    font-weight: 700;
    font-size: 26px;
    line-height: 1;
    color: var(--white);
    margin-top: -6px;
  }
  .place-name {
    position: absolute;
    left: 0;
    width: 830px;
    top: 468px;
    display: flex;
    align-items: center;
    justify-content: center;
    gap: 12px;
    font-family: "Josefin Sans", sans-serif;
    font-weight: 400;
    font-size: 52px;
    line-height: 1;
    letter-spacing: 4px;
    color: var(--title-yellow);
  }
  .place-dot {
    width: 13px;
    height: 13px;
    border-radius: 50%;
    background: var(--white);
    margin-top: -6px;
  }
  .author {
    position: absolute;
    left: 0;
    width: 830px;
    top: 535px;
    text-align: center;
    font-family: "Comic Neue", sans-serif;
    font-weight: 700;
    font-size: 17px;
    color: var(--ink);
  }
  .caption {
    position: absolute;
    left: 0;
    width: 1230px;
    top: 858px;
    margin: 0;
    text-align: center;
    font-family: "PT Sans Narrow", sans-serif;
    font-weight: 400;
    font-size: 86px;
    line-height: 1;
    color: #000;
  }
</style>
</head>
<body>
<main class="canvas">
  <section class="cover">
    <svg class="cover-shapes" width="802" height="802" viewBox="0 0 802 802" aria-hidden="false">
      <defs>
        <linearGradient id="skyline-fade" x1="0" y1="0" x2="0" y2="1">
          <stop offset="0" stop-color="#d6007f" stop-opacity="0"/>
          <stop offset="0.35" stop-color="#d6007f" stop-opacity="0.45"/>
          <stop offset="1" stop-color="#d6007f" stop-opacity="0.8"/>
        </linearGradient>
      </defs>
      <rect class="skyline-area" x="0" y="520" width="802" height="230" fill="url(#skyline-fade)" role="img" aria-label="Faint city skyline silhouette of the suburb"/>
      <path class="band-top" d="M0 0 H802 V62 C520 22 170 8 0 98 Z" fill="var(--sunflower)"/>
      <path class="band-bottom" d="M0 802 V737 C45 675 110 655 172 695 C320 770 520 795 802 737 V802 Z" fill="var(--sunflower)"/>
    </svg>
    <div class="cover-text">
      <div class="count-box">1000</div>
      <div class="count-rule"></div>
      <h1 class="main-title">Spørsmål</h1>
      <div class="connector">
        <span class="connector-line"></span>
        <span class="connector-word">om</span>
        <span class="connector-line"></span>
      </div>
      <div class="place-name">
        <span class="place-dot"></span>
        <span>KVERNHAUGEN</span>
        <span class="place-dot"></span>
      </div>
      <div class="author">Helge Myrvold</div>
    </div>
  </section>
  <p class="caption">BOOK COVER</p>
</main>
</body>
</html>
```